Corvy

Electronic Repairs for OEM's Industrial electronic repairs, consumer audio visual, Projectors

Target Market(s)

manufacturer of electronics (OEM), business, Government, then Consumer

Industry/Entity Type

Electronic Repair

Contact Information for Business Card

Board Repair, Projectors

Font styles to use
Serif

Colors
0054AA
0677BA
7BADD7
CADEEF
E8F1F8

Requirements
Must have
• projector, led wall image
Nice to have
• professional looking business card.
Should not have
• unsure

```html
<!DOCTYPE html>
<html lang="en">
<head>
<meta charset="utf-8">
<title>Corvy Electronics, Inc. — Business Card</title>
<link rel="stylesheet" href="https://fonts.googleapis.com/css2?family=Montserrat:wght@700;800&family=Inter:wght@300;400;600;700&family=Roboto+Condensed:wght@400;700&display=swap">
<style>
  :root {
    --brand-deep: #0054AA;
    --brand-mid: #0677BA;
    --brand-soft: #7BADD7;
    --brand-pale: #CADEEF;
    --brand-mist: #E8F1F8;
    --ink: #111418;
    --card-white: #FAFBFC;
    --page-bg: #E4E8EC;
    --projector-tone: #1E5F78;
    --ledwall-tone: #C21FD0;
    --board-tone: #1D4E8F;
  }
  * { box-sizing: border-box; margin: 0; padding: 0; }
  html, body { width: 1200px; height: 840px; overflow: hidden; }
  body { background: var(--page-bg); position: relative; font-family: "Inter", sans-serif; }

  .business-card {
    position: absolute; left: 100px; top: 134px;
    width: 1000px; height: 572px;
    background: var(--card-white);
    border-radius: 34px;
    overflow: hidden;
    box-shadow: 0 14px 40px rgba(0, 40, 90, 0.18);
  }
  .card-band { position: absolute; inset: 0; width: 1000px; height: 572px; }

  .service-photo {
    position: absolute; border-radius: 50%;
    width: 216px; height: 216px;
    border: 5px solid #fff;
    box-shadow: 0 4px 14px rgba(0, 0, 0, 0.25);
  }
  .photo-projector { left: 610px; top: 40px;
    background: radial-gradient(circle at 55% 55%, #B8B4F0 0%, #3A7F9A 18%, var(--projector-tone) 55%, #0D2F40 100%); }
  .photo-ledwall { left: 752px; top: 150px;
    background: linear-gradient(160deg, #E24BEF 0%, var(--ledwall-tone) 60%, #6E0F7E 100%); }
  .photo-boardwork { left: 680px; top: 300px;
    background: radial-gradient(circle at 40% 35%, #B9C9DA 0%, #3A6DAA 35%, var(--board-tone) 70%, #0C2A57 100%); }

  .card-content { position: absolute; left: 76px; top: 36px; width: 560px; }
  .company-name {
    font-family: "Montserrat", sans-serif; font-weight: 800;
    font-size: 104px; line-height: 0.95; letter-spacing: -1px;
    color: var(--brand-deep);
  }
  .company-suffix {
    font-weight: 300; font-size: 40px; line-height: 1.1;
    letter-spacing: 1px; color: var(--brand-mid);
  }
  .company-tagline {
    margin-top: 16px;
    font-weight: 700; font-size: 23px; line-height: 1.25;
    color: var(--brand-deep);
  }
  .service-list { list-style: none; margin-top: 18px; }
  .service-list li {
    display: flex; align-items: center; gap: 16px;
    font-size: 27px; font-weight: 400; line-height: 1.35; color: var(--ink);
  }
  .tick-icon { width: 24px; height: 24px; flex: none; }
  .contact-phone {
    margin-top: 16px;
    font-family: "Montserrat", sans-serif; font-weight: 800;
    font-size: 38px; line-height: 1.1; color: var(--brand-deep);
    white-space: nowrap;
  }
  .contact-email {
    font-family: "Roboto Condensed", sans-serif; font-weight: 700;
    font-size: 33px; line-height: 1.15; color: var(--ink);
    white-space: nowrap;
  }
  .contact-address {
    font-family: "Roboto Condensed", sans-serif; font-weight: 400;
    font-size: 24px; line-height: 1.2; color: var(--ink);
    white-space: nowrap;
  }
</style>
</head>
<body>
  <article class="business-card">
    <svg class="card-band" viewBox="0 0 1000 572" aria-hidden="true">
      <path d="M630,0 C790,140 810,400 700,572 L1000,572 L1000,0 Z" fill="var(--brand-deep)"/>
      <path d="M630,0 C660,26 690,56 712,90 C700,50 680,20 660,0 Z" fill="var(--brand-mid)"/>
    </svg>

    <div class="service-photo photo-projector" role="img" aria-label="Photo of a ceiling-mounted projector casting light"></div>
    <div class="service-photo photo-ledwall" role="img" aria-label="Photo of magenta LED wall panels"></div>
    <div class="service-photo photo-boardwork" role="img" aria-label="Photo of tweezers working on a circuit board"></div>

    <div class="card-content">
      <h1 class="company-name">CORVY</h1>
      <p class="company-suffix">ELECTRONICS, INC.</p>
      <p class="company-tagline">Electronic Repairs for OEM's<br>Industrial electronic repairs,<br>consumer audio visual, Projectors</p>
      <ul class="service-list">
        <li><svg class="tick-icon" viewBox="0 0 24 24" aria-hidden="true"><circle cx="12" cy="12" r="12" fill="var(--brand-deep)"/><path d="M6.5 12.5l3.5 3.5 7.5-8" fill="none" stroke="#fff" stroke-width="2.6" stroke-linecap="round" stroke-linejoin="round"/></svg>Projector</li>
        <li><svg class="tick-icon" viewBox="0 0 24 24" aria-hidden="true"><circle cx="12" cy="12" r="12" fill="var(--brand-deep)"/><path d="M6.5 12.5l3.5 3.5 7.5-8" fill="none" stroke="#fff" stroke-width="2.6" stroke-linecap="round" stroke-linejoin="round"/></svg>Led wall image</li>
        <li><svg class="tick-icon" viewBox="0 0 24 24" aria-hidden="true"><circle cx="12" cy="12" r="12" fill="var(--brand-deep)"/><path d="M6.5 12.5l3.5 3.5 7.5-8" fill="none" stroke="#fff" stroke-width="2.6" stroke-linecap="round" stroke-linejoin="round"/></svg>Board Repair</li>
      </ul>
      <p class="contact-phone">CALL US 555-210 3847</p>
      <p class="contact-email">info@corvyelectronicrepairs.com</p>
      <p class="contact-address">412 Birchwood Road, Fairview, Alaska 99000</p>
    </div>
  </article>
</body>
</html>
```